Print design needed to improve the layout and look of some existing documents

We need someone to take a couple of existing documents that we have and make them look much better using our existing logo and corporate colors etc. We require these to be delivered in a format that will allow our staff to edit the content as necessary via Microsoft word for conversion once finalized into a PDF. Ideally, we will also be able to use this as a newsletter template or for other documents that might be required in our business. www.corvelleadvisory.com.au
Updates

Target Market(s)

Business owners, executives, retirees

Industry/Entity Type

Financial Service

Font styles to use
Serif

Requirements
Must have
• Design that uses our existing branding and colors. It also needs to be ina form that we can edit the content / update easily. Ideally the format / layout could also be used for other documents such as short newsletters etc.
Nice to have
• Fresh, simple and crisp. Very professional looking.
Should not have
• strange fonts, weird layouts.

```html
<!DOCTYPE html>
<html lang="en">
<head>
<meta charset="utf-8">
<title>Corvelle Advisory – Financial Services Guide, page 6</title>
<link href="https://fonts.googleapis.com/css2?family=Source+Sans+3:wght@400;600&display=swap" rel="stylesheet">
<style>
  :root {
    --backdrop: #dcdcdc;
    --sheet: #ffffff;
    --panel: #f5f5f5;
    --ink: #3a3a3a;
    --brand-blue: #1a8fd0;
    --brand-green: #6cb33f;
    --brand-dark: #333333;
    --photo-light: #d6d6d6;
    --photo-mid: #93b9b0;
    --photo-warm: #9a6248;
  }
  * { margin: 0; padding: 0; box-sizing: border-box; }
  html, body {
    width: 1200px; height: 793px; overflow: hidden;
    background: var(--backdrop);
    font-family: "Source Sans 3", sans-serif;
    color: var(--ink);
  }
  .sheet {
    position: absolute; left: 318px; top: 0;
    width: 564px; height: 793px;
    background: var(--sheet);
    padding: 18px;
  }
  .panel {
    position: relative;
    width: 528px; height: 757px;
    background: var(--panel);
  }
  .brand {
    position: absolute; left: 21px; top: 26px;
    display: flex; align-items: center; gap: 7px;
  }
  .brand-dot {
    width: 12px; height: 12px; border-radius: 50%;
    background: var(--brand-blue);
  }
  .brand-name {
    font-size: 18px; font-weight: 400; letter-spacing: 0.5px;
    color: var(--brand-dark);
  }
  .column {
    position: absolute; top: 78px;
    font-size: 9.9px; line-height: 12.4px;
  }
  .column-left { left: 20px; width: 226px; }
  .column-right { left: 275px; width: 232px; }
  .section-title {
    font-size: 10px; line-height: 10.6px; font-weight: 600;
    color: var(--brand-blue); margin-bottom: 13px;
  }
  .column-right .section-title { margin-bottom: 14px; }
  .column-left p { margin-bottom: 12.4px; }
  .info-list { list-style: none; }
  .info-list li {
    position: relative; padding-left: 13px; margin-bottom: 6.6px;
    line-height: 14.3px;
  }
  .info-list li::before {
    content: ""; position: absolute; left: 0; top: 5.5px;
    width: 3.5px; height: 3.5px; border-radius: 50%;
    background: var(--brand-blue);
  }
  .team-photo {
    position: absolute; left: 0; top: 438px;
    width: 528px; height: 242px;
    background: linear-gradient(160deg, var(--photo-light) 0%, var(--photo-mid) 50%, var(--photo-warm) 100%);
  }
  .footer-band {
    position: absolute; left: 0; top: 726px;
    width: 528px; height: 24px;
    background: var(--brand-blue);
    display: flex; align-items: center;
  }
  .footer-details {
    flex: 1; padding-left: 20px;
    font-size: 7.4px; color: #ffffff;
    display: flex; align-items: center; gap: 4px;
  }
  .footer-details svg { width: 8px; height: 8px; margin-left: 5px; }
  .page-number {
    width: 50px; height: 24px;
    background: var(--brand-green);
    color: #ffffff; font-weight: 600; font-size: 12px;
    display: flex; align-items: center; justify-content: center;
  }
</style>
</head>
<body>
  <div class="sheet">
    <div class="panel">
      <div class="brand">
        <span class="brand-dot"></span>
        <span class="brand-name">CORVELLE ADVISORY</span>
      </div>

      <section class="column column-left">
        <h2 class="section-title">How do you know we will manage your<br>Investments appropriately?</h2>
        <p>We will only recommend an MDA service where it is in your best interests and suitable for you.</p>
        <p>Once in place, we will only make changes to your investments which are consistent with our understanding of your financial needs, objectives and circumstances. We will also comply at all times with the MDA service agreement and the Investment Program that we agree with you.</p>
        <p>It is important that you immediately inform us of any significant changes to your financial needs, objectives or circumstances.</p>
        <p>We will undertake an annual review to ensure that the MDA Service and the Investment Program remain appropriate for you. This review will be documented in a Record of Advice.</p>
        <p>You will have access to on-line reporting and /or hard copy statements for your account. This will allow you to view the transactions undertaken on your behalf and to understand their impact on your account.</p>
      </section>

      <section class="column column-right">
        <h2 class="section-title">Other Important Information</h2>
        <ul class="info-list">
          <li>We will contact you for instructions where action is required on your account which is outside our authority.</li>
          <li>The MDA Service does not include a custodial or depository service, as this is facilitated through the regulated platform.</li>
          <li>You can cancel the MDA Service or request changes to the Investment Program at any time by notifying us in writing.</li>
          <li>This FSG complies with ASIC Class Order 04/194.</li>
        </ul>
      </section>

      <div class="team-photo" role="img" aria-label="Photo of the advisory team seated around a meeting table"></div>

      <footer class="footer-band">
        <div class="footer-details">
          <span>Corvelle Advisory Pty Ltd &nbsp;•&nbsp; AFSL 000000 &nbsp;•&nbsp; ABN 00 000 000 000</span>
          <svg viewBox="0 0 10 10" aria-hidden="true"><path d="M4 6 L6 4 M3.2 4.6 L2 5.8 a1.6 1.6 0 0 0 2.2 2.2 L5.4 6.8 M4.6 3.2 L5.8 2 a1.6 1.6 0 0 1 2.2 2.2 L6.8 5.4" fill="none" stroke="#fff" stroke-width="0.9"/></svg>
          <span>www.corvelleadvisory.com.au</span>
        </div>
        <div class="page-number">6</div>
      </footer>
    </div>
  </div>
</body>
</html>
```